Local Flower Farm Needs Business Card Design

I need business cards designed for a flower farm based in Eudora, Kansas.
Business Info:
We are a local cut flower farm located in Eudora, Kansas, founded by Corinne Haldwick. What started as a passion for agriculture and search for more joy in daily life has blossomed into a small business dedicated to providing the community with beautiful, fresh, and sustainable flowers. We specialize in local, seasonal blooms, ensuring that every petal reflects the care and dedication we pour into our craft. Our mission is to deliver the highest quality flowers directly to our customers through local farmers markets and to florists who share our commitment to sustainability. Join us in celebrating the beauty of nature, one bloom at a time!
Contact Details:
Corinne Haldwick
Owner
Phone 913-555-0147
Facebook: Rosalind Thorpe Gardens
Instagram: @RosalindThorpeGardens
Website: RosalindThorpeGardens.example
Target Market(s)
Wholesale to Florists and Direct to Consumer via Farmers Market
Industry/Entity Type
Florist, Farm
Contact Information for Business Card
Name, Contact Info, Logo
Look and feel
Each slider illustrates characteristics of the customer's brand and the style your logo design should communicate.

```html
<!DOCTYPE html>
<html lang="en">
<head>
<meta charset="utf-8">
<title>Rosalind Thorpe Gardens – Business Card</title>
<link rel="stylesheet" href="https://fonts.googleapis.com/css2?family=Libre+Baskerville:wght@400;700&family=Outfit:wght@400&display=swap">
<style>
  :root {
    --backdrop: #9a9a9a;
    --paper: #ffffff;
    --ink: #0b2830;
    --ink-soft: #3d5359;
    --rule: #d4d8d9;
    --on-dark: #ffffff;
  }
  * { box-sizing: border-box; margin: 0; padding: 0; }
  html, body { width: 1093px; height: 1200px; overflow: hidden; }
  body { background: var(--backdrop); position: relative; font-family: "Outfit", sans-serif; }

  .card { position: absolute; left: 265px; width: 579px; height: 356px; border-radius: 26px; }
  .card--front { top: 226px; background: var(--paper); color: var(--ink); }
  .card--back { top: 621px; background: var(--ink); color: var(--on-dark); }

  .brand-mark {
    position: absolute; border-radius: 50%;
    display: flex; align-items: center; justify-content: center; text-align: center;
    font-family: "Libre Baskerville", serif; font-weight: 400;
    letter-spacing: 0.08em; text-transform: uppercase; line-height: 1.5;
  }
  .card--front .brand-mark {
    left: 40px; top: 92px; width: 182px; height: 182px;
    border: 1px solid var(--ink); color: var(--ink); font-size: 15px;
  }
  .card--back .brand-mark {
    left: 192px; top: 63px; width: 196px; height: 196px;
    border: 1px solid var(--on-dark); color: var(--on-dark); font-size: 16px;
  }

  .divider { position: absolute; left: 248px; top: 74px; width: 1px; height: 209px; background: var(--rule); }

  .identity { position: absolute; left: 268px; top: 95px; }
  .identity__name {
    font-family: "Libre Baskerville", serif; font-weight: 400;
    font-size: 19px; letter-spacing: 0.02em; text-transform: uppercase; line-height: 1.1;
  }
  .identity__role { font-size: 16px; color: var(--ink); margin-top: 2px; }

  .contact-list { position: absolute; left: 268px; top: 158px; list-style: none; }
  .contact-list li { display: flex; align-items: center; height: 26px; font-size: 17px; }
  .contact-icon {
    width: 21px; height: 21px; border: 1px solid var(--ink); border-radius: 50%;
    margin-right: 5px; flex: none; display: flex; align-items: center; justify-content: center;
  }

  .back-url {
    position: absolute; left: 0; right: 0; top: 300px; text-align: center;
    font-size: 17px; letter-spacing: 0.06em;
  }
</style>
</head>
<body>
  <section class="card card--front">
    <div class="brand-mark">Rosalind<br>Thorpe<br>Gardens</div>
    <div class="divider"></div>
    <div class="identity">
      <h1 class="identity__name">Corinne Haldwick</h1>
      <p class="identity__role">Owner</p>
    </div>
    <ul class="contact-list">
      <li>
        <span class="contact-icon">
          <svg width="11" height="11" viewBox="0 0 24 24" aria-hidden="true"><path d="M6.6 10.8a15.1 15.1 0 0 0 6.6 6.6l2.2-2.2a1 1 0 0 1 1-.25 11.4 11.4 0 0 0 3.6.57 1 1 0 0 1 1 1V20a1 1 0 0 1-1 1A17 17 0 0 1 3 4a1 1 0 0 1 1-1h3.5a1 1 0 0 1 1 1c0 1.25.2 2.45.57 3.57a1 1 0 0 1-.25 1z" fill="#0b2830"/></svg>
        </span>913-555-0147
      </li>
      <li><span class="contact-icon"></span>Rosalind Thorpe Gardens</li>
      <li><span class="contact-icon"></span>@RosalindThorpeGardens</li>
      <li>
        <span class="contact-icon">
          <svg width="13" height="13" viewBox="0 0 24 24" aria-hidden="true" fill="none" stroke="#0b2830" stroke-width="2"><circle cx="12" cy="12" r="9"/><ellipse cx="12" cy="12" rx="4" ry="9"/><path d="M3 12h18M5 7h14M5 17h14"/></svg>
        </span>RosalindThorpeGardens.example
      </li>
    </ul>
  </section>

  <section class="card card--back">
    <div class="brand-mark">Rosalind<br>Thorpe<br>Gardens</div>
    <p class="back-url">RosalindThorpeGardens.example</p>
  </section>
</body>
</html>
```